A design led business card for the construction industry

High-end business card to match logo. White logo on dark grey/off black to the front. Matching dark font on white to back, possibly with logo design again.

We offer construction and project management services to commercial and private clients in the UK. Projetcs range from newbuilds, conversion of listed buildings and refurbishments and extensions of existing homes. Our focus is on quality and attention to detail using the highest skills.

Contact Information for Business Card

Name; Dorian Keble BSc
Position; Project Manager
Mobile; 07962 408 175
Tel; 01632 960457
email; dorian@stonevale.co.uk
web; www.stonevale.co.uk
Address; Ashbury on Wey, KX4 7PW

Colors

Designer to choose only greyscale colors for use in the design.

Requirements
Must have
• To include the below description of the business,

CONSTRUCTION - PROJECT MANAGEMENT
Nice to have
• The posibility of the top back of the card being used as a ruler. So will have a measurement to scale in mm or an architect scale of 1:50
Should not have
• Should not be portrait

```html
<!DOCTYPE html>
<html lang="en">
<head>
<meta charset="utf-8">
<title>Stonevale – Business Card</title>
<link rel="stylesheet" href="https://fonts.googleapis.com/css2?family=Arimo:wght@400;700&display=swap">
<style>
  :root {
    --backdrop: #565656;
    --card-light: #ffffff;
    --card-dark: #232323;
    --ink: #111111;
    --ink-reverse: #ffffff;
    --tagline: #bdbdbd;
  }
  * { margin: 0; padding: 0; box-sizing: border-box; }
  html, body { width: 1065px; height: 1200px; overflow: hidden; }
  body {
    background: var(--backdrop);
    font-family: "Arimo", Arial, sans-serif;
    position: relative;
  }
  .card {
    position: absolute;
    width: 583px;
    height: 362px;
    box-shadow: 2px 3px 4px rgba(0,0,0,0.45);
  }
  .card--back {
    left: 292px; top: 218px;
    background: var(--card-light);
    border-radius: 0 181px 181px 0;
    color: var(--ink);
  }
  .card--front {
    left: 263px; top: 623px;
    background: var(--card-dark);
    border-radius: 181px 0 0 181px;
    color: var(--ink-reverse);
  }
  .contact {
    position: absolute;
    left: 38px; top: 89px;
  }
  .contact__name { font-size: 20px; font-weight: 700; line-height: 1.1; }
  .contact__name .credential { font-weight: 400; }
  .contact__role { font-size: 17px; line-height: 1.2; margin-top: 0; }
  .contact__list { list-style: none; margin-top: 15px; }
  .contact__item {
    display: flex; align-items: center;
    font-size: 17px; height: 21px;
  }
  .contact__item svg { width: 15px; height: 15px; margin-right: 6px; flex: none; }
  .contact__address { font-size: 17px; margin-top: 16px; }
  .wordmark {
    position: absolute;
    font-weight: 400;
    letter-spacing: 0.45em;
    padding-left: 0.45em;
    line-height: 1.15;
    white-space: nowrap;
    transform: translateX(-50%);
  }
  .card--back .wordmark { left: 422px; top: 226px; font-size: 24px; }
  .card--front .wordmark { left: 292px; top: 211px; font-size: 30px; }
  .tagline {
    position: absolute;
    left: 292px; top: 262px;
    transform: translateX(-50%);
    font-size: 14px;
    color: var(--tagline);
    white-space: nowrap;
  }
</style>
</head>
<body>
  <section class="card card--back">
    <div class="contact">
      <p class="contact__name">DORIAN KEBLE <span class="credential">BSc</span></p>
      <p class="contact__role">Project Manager</p>
      <ul class="contact__list">
        <li class="contact__item">
          <svg viewBox="0 0 16 16" aria-hidden="true"><rect x="3.5" y="1" width="9" height="14" rx="1.5" fill="none" stroke="currentColor" stroke-width="1.6"/><circle cx="8" cy="12.5" r="0.9" fill="currentColor"/></svg>
          07962 408 175
        </li>
        <li class="contact__item">
          <svg viewBox="0 0 16 16" aria-hidden="true"><path d="M4 1.5 6.2 4.5 4.8 6c.8 2 2.6 3.8 4.6 4.6l1.5-1.4 3 2.2-1.3 2.3c-5 0-10.8-5.8-10.8-10.8z" fill="none" stroke="currentColor" stroke-width="1.5" stroke-linejoin="round"/></svg>
          01632 960457
        </li>
        <li class="contact__item">
          <svg viewBox="0 0 16 16" aria-hidden="true"><rect x="1" y="3.5" width="14" height="9" fill="currentColor"/><path d="M1 3.5 8 9l7-5.5" fill="none" stroke="#fff" stroke-width="1"/></svg>
          dorian@stonevale.co.uk
        </li>
        <li class="contact__item">
          <svg viewBox="0 0 16 16" aria-hidden="true"><g fill="none" stroke="currentColor" stroke-width="1.2"><circle cx="8" cy="8" r="6.5"/><ellipse cx="8" cy="8" rx="3" ry="6.5"/><path d="M1.5 8h13M2.5 4.8h11M2.5 11.2h11"/></g></svg>
          www.stonevale.co.uk
        </li>
      </ul>
      <p class="contact__address">Ashbury on Wey, KX4 7PW</p>
    </div>
    <p class="wordmark">STONEVALE</p>
  </section>

  <section class="card card--front">
    <p class="wordmark">STONEVALE</p>
    <p class="tagline">CONSTRUCTION - PROJECT MANAGEMENT</p>
  </section>
</body>
</html>
```